Quorva - corporate Business Card

We need a good look and innovative business card for a new start up company based in Los Angeles called "Quorva". We are in a payment business, including payment card, app, and ewallet. We are expert in online payment and Card not present (CNP) transaction.
We need an innovative, modern business card.

Our logo font is Aero Matics

Target Market(s)

Startup - Bank - Online Payment - Card Manufacturing

Industry/Entity Type

Startup

Contact Information for Business Card

phone: 555 014 7396 - Address: 4172 Marlowe blvd, Cylver City, CA 90299

Requirements
Must have
• Message: innovative, professional, expert, high tech, trust, online payment expert, security
Nice to have
• no comment
Should not have
• no Comment

```html
<!DOCTYPE html>
<html lang="en">
<head>
<meta charset="utf-8">
<title>Quorva – Business Card</title>
<link rel="stylesheet" href="https://fonts.googleapis.com/css2?family=Exo+2:wght@600&family=Source+Sans+3:wght@400;600&display=swap">
<style>
  :root {
    --brand-red: #b81f31;
    --card-white: #ffffff;
    --ink-grey: #4f4f4f;
    --backdrop: #e8e5e1;
    --card-shadow: rgba(0, 0, 0, 0.18);
  }
  * { box-sizing: border-box; margin: 0; padding: 0; }
  html, body {
    width: 1200px;
    height: 987px;
    overflow: hidden;
    background: var(--backdrop);
  }
  .card {
    position: absolute;
    left: 292px;
    width: 616px;
    height: 350px;
    background: var(--card-white);
    box-shadow: 0 2px 6px var(--card-shadow);
    overflow: hidden;
    font-family: "Source Sans 3", sans-serif;
    color: var(--ink-grey);
  }
  .card--front { top: 130px; }
  .card--back  { top: 506px; }

  .front-band {
    position: absolute;
    inset: 0;
  }
  .front-mark {
    position: absolute;
    left: 109px;
    top: 90px;
    width: 165px;
    height: 165px;
    background: var(--brand-red);
  }
  .wordmark {
    position: absolute;
    font-family: "Exo 2", sans-serif;
    font-weight: 600;
    color: var(--brand-red);
    line-height: 1;
    letter-spacing: 1px;
    white-space: nowrap;
  }
  .front-wordmark {
    right: 38px;
    top: 138px;
    font-size: 68px;
  }
  .contact-block {
    position: absolute;
    right: 38px;
    text-align: right;
    font-size: 16px;
    line-height: 21px;
    white-space: nowrap;
  }
  .person { top: 36px; }
  .person-name {
    font-size: 21px;
    font-weight: 600;
    color: var(--brand-red);
    line-height: 24px;
  }
  .address-block { top: 252px; }
  .phone-label { color: var(--brand-red); font-weight: 600; }

  .back-mark {
    position: absolute;
    left: 115px;
    top: 117px;
    width: 116px;
    height: 116px;
    border-radius: 50%;
    background: var(--brand-red);
  }
  .back-wordmark {
    left: 250px;
    top: 143px;
    font-size: 64px;
  }
  .website {
    position: absolute;
    left: 0;
    right: 0;
    top: 290px;
    text-align: center;
    font-size: 15px;
    letter-spacing: 6px;
    color: var(--ink-grey);
  }
</style>
</head>
<body>
  <section class="card card--front">
    <svg class="front-band" width="616" height="350" viewBox="0 0 616 350" aria-hidden="true">
      <rect width="616" height="350" fill="var(--brand-red)"/>
      <path d="M118,0 H616 V350 H183 C70,322 12,250 16,180 C20,100 62,32 118,0 Z" fill="var(--card-white)"/>
    </svg>
    <div class="front-mark" aria-hidden="true"></div>
    <div class="wordmark front-wordmark">quorva</div>
    <div class="contact-block person">
      <div class="person-name">DANIEL REYES</div>
      <div>CEO&amp;Founder</div>
      <div>daniel@quorva.com</div>
    </div>
    <div class="contact-block address-block">
      <div><span class="phone-label">P:</span> 555 014 7396</div>
      <div>4172 Marlowe blvd</div>
      <div>Marden Vale, CA 90299</div>
    </div>
  </section>

  <section class="card card--back">
    <div class="back-mark" aria-hidden="true"></div>
    <div class="wordmark back-wordmark">quorva</div>
    <div class="website">www.quorva.com</div>
  </section>
</body>
</html>
```